One business card required with 2 company logos and 2 people's details

One business card required.
No preference on design - One side could show the 2 different business logos for the companies we own. The reverse could have the details shown below.
Another option could be one business one side and one business on the reverse. Happy to receive designs.

Dora Pellham
07700 913 286
Rowena Tindall
07700 958 137

website: quietmeadowbloom.co.uk
email: info@quietmeadowbloom.co.uk

website: brightharbourevents.co.uk
email: info:brightharbourevents.co.uk

May be nice to have icons instead of the words email/website?

I have included different versions of the logos to help with your design.

Contact Information for Business Card

see project overview

Requirements
Must have
• both company logos, both contact names and contact details

```html
<!DOCTYPE html>
<html lang="en">
<head>
<meta charset="utf-8">
<title>Business Card – Bright Harbour Events &amp; Quiet Meadow Bloom</title>
<link rel="stylesheet" href="https://fonts.googleapis.com/css2?family=Montserrat:wght@300;400;500&display=swap">
<style>
  :root {
    --page: #6b6b6b;
    --card-dark: #232324;
    --card-light: #ffffff;
    --accent-blue: #1b86e0;
    --edge-blue: #1447c9;
    --divider-blue: #2a5fd6;
    --text-light: #f2f2f2;
    --brand-ink: #1d3fb8;
  }
  * { box-sizing: border-box; margin: 0; padding: 0; }
  html, body {
    width: 1200px;
    height: 800px;
    overflow: hidden;
    background: var(--page);
    font-family: "Montserrat", sans-serif;
  }
  .canvas {
    width: 1200px;
    height: 800px;
    display: flex;
    align-items: center;
    justify-content: center;
    gap: 60px;
  }
  .card {
    width: 525px;
    height: 330px;
    border-radius: 22px;
    position: relative;
    box-shadow: 0 3px 0 var(--edge-blue), 0 18px 30px rgba(0,0,0,0.35);
    overflow: hidden;
  }
  /* Contact side */
  .card--contacts {
    background: var(--card-dark);
    color: var(--text-light);
    display: flex;
    flex-direction: column;
    justify-content: center;
    padding: 0 40px;
  }
  .people {
    display: flex;
    align-items: stretch;
    justify-content: center;
    gap: 16px;
    margin-bottom: 52px;
  }
  .person { color: var(--accent-blue); }
  .person__name {
    font-weight: 400;
    font-size: 24px;
    line-height: 1.05;
    letter-spacing: 0.2px;
  }
  .person__phone {
    font-weight: 400;
    font-size: 14px;
    letter-spacing: 1px;
    padding-left: 22px;
  }
  .people__divider {
    width: 1px;
    background: var(--accent-blue);
  }
  .contact-lines {
    font-weight: 400;
    font-size: 13px;
    line-height: 1.55;
    text-align: center;
    letter-spacing: 0.3px;
  }
  /* Logo side */
  .card--brands {
    background: var(--card-light);
    display: flex;
    align-items: center;
    justify-content: center;
  }
  .brand {
    width: 210px;
    display: flex;
    align-items: center;
    justify-content: center;
    gap: 10px;
    color: var(--brand-ink);
    font-weight: 500;
    font-size: 20px;
    line-height: 1.2;
    text-align: center;
  }
  .brand__dot {
    flex: none;
    width: 12px;
    height: 12px;
    border-radius: 50%;
    background: var(--brand-ink);
  }
  .brands__divider {
    width: 1px;
    height: 170px;
    background: var(--divider-blue);
    margin: 0 18px;
  }
</style>
</head>
<body>
<main class="canvas">
  <section class="card card--contacts" aria-label="Contact side">
    <div class="people">
      <div class="person">
        <p class="person__name">Dora Pellham</p>
        <p class="person__phone">07700 913 286</p>
      </div>
      <span class="people__divider"></span>
      <div class="person">
        <p class="person__name">Rowena Tindall</p>
        <p class="person__phone">07700 958 137</p>
      </div>
    </div>
    <div class="contact-lines">
      <p>info@quietmeadowbloom.co.uk| www.quietmeadowbloom.co.uk</p>
      <p>info:brightharbourevents.co.uk | www.brightharbourevents.co.uk</p>
    </div>
  </section>

  <section class="card card--brands" aria-label="Company names side">
    <div class="brand brand--events">
      <span class="brand__dot"></span>
      <span class="brand__name">Bright Harbour Events</span>
    </div>
    <span class="brands__divider"></span>
    <div class="brand brand--bloom">
      <span class="brand__dot"></span>
      <span class="brand__name">Quiet Meadow Bloom</span>
    </div>
  </section>
</main>
</body>
</html>
```